MyName is TapLedger .... Killer of Business Cards!!! WANT a KickAss Design Landing Page :)

How 'TapLedger' works:
- with a unique name for each country, like a personalise car plate number
- our platform links through a 'Quick Text' keyword short code
- TapLedger platform will respond with downloaded ready full contact business file link
- this is designed to be downloaded in just '3 clicks' into your Contacts Folder
- any changes,,updates, images, online profiles can be made in real time updates
- TapLedger provides a backend login to manage individual account and is ready
Enterprise model for larger staff companies
- platform is international ready and have launched
Australia, in September 2019.

Yes, your whole business card and online profile in '3' simple clicks. No '20-30 mins' of typing the business card contacts details into mobile phones.
** Fact: 88% of business cards are lost of thrown out within 7 days.
(https://www.plumfinchstats.com/business-card-statistics.html) **

NZ ClipStream
https://vidhost.example/q7Rt2LmP9xZ

**current websites are www.tapledge.co.nz www.taplink.com.au www.tapledgerau.com www.tapledgerus.com **

Target Market(s)

Anybody who uses a business card, from trades person, real estate agents, consultants, bankers (in NZ/AU with have plumbers, financial advisors, real estate agents, mortgage brokers, sports agents, Telcos etc etc)

Industry/Entity Type

Business Software

Coding

Coded - Design and coding required

Number of Pages Required

4 page

Font styles to use
Other font styles liked:
• libre franklin black

Requirements
Must have
• TapLedger a simple 'in delivery' and smart 'in innovation' solution so our message is Simple, Clear and Inquisitive. We would like a converting landing page because we are selling Nimble Cloud Suite at low-entry cost and no-contract. IWe want to direct clients to a name reservation platform to a virtual business card that uses our Nimble Core Engine. We will require some code at the back to link the name reservation and sign up source code(javascript). This web/landing page fresh page is required because we have recently changed our marketing strategy to be purely digital marketing in Chatterbook and Snapgrid Ads from now on. We would like this to be exciting graphically to grab attention, inquisitive enough to check your name availability and follow through with call to action with the right colours and graphics images. We plan to test the right pitch offering until we get the markets feedback on the best offering/re-design and then push harder with more CB and SG Ads. ( **we plan to continue multiple regular campaigns as the business has now change our strategy due to covid-19 and we will focus mainly on direct to consumers**)

Also:
2 buttons: Signup and a Check availability little form to allow a java script to be added/HTML5/CB advertising/Super Inviting to check 'YOUR UNIQUE NAME' is available. Then clicking the to reserve the name to purchase our Quick Text/Eco-Friendly/Relevant to todays tech and Low Cost service. We will be offering Promo codes for each campaign.
No Apps. Works with SMS, any smartphone, country specific, enterprise ready, and CONTACTLESS ....
Nice to have
• Personal feeling. Unique choice of 'your name' as this is your business and social profile in one. Strong independent images and confident to share with anybody their profile by just sharing their name.
Should not have
• Open currently....

```html
<!DOCTYPE html>
<html lang="en">
<head>
<meta charset="utf-8">
<title>TapLedger – Share Your Business Details in One Quick Text</title>
<link rel="stylesheet" href="https://fonts.googleapis.com/css2?family=Libre+Franklin:ital,wght@0,400;0,500;0,600;0,700;0,800;0,900;1,400;1,600;1,700;1,800&display=swap">
<style>
:root{
  --navy:#1c2a5e;
  --navy-deep:#1a2a62;
  --teal:#17726f;
  --mint:#dff0ee;
  --mint-dark:#cfe7e4;
  --ink:#202a44;
  --body:#3c4150;
  --footer:#131b38;
  --white:#ffffff;
}
*{box-sizing:border-box;margin:0;padding:0}
html,body{width:1200px;height:3844px;overflow:hidden}
body{position:relative;font-family:"Libre Franklin",Arial,sans-serif;color:var(--body);background:var(--white)}
.abs{position:absolute}
.btn{position:absolute;display:flex;align-items:center;justify-content:center;border-radius:30px;color:#fff;font-weight:700;font-size:15px;letter-spacing:.3px;text-transform:uppercase;text-decoration:none;box-shadow:0 4px 10px rgba(0,0,0,.22)}
.btn-teal{background:var(--teal)}
.btn-navy{background:var(--navy)}

/* header */
.site-header{position:absolute;top:0;left:0;width:1200px;height:93px;background:#fff}
.brand{position:absolute;display:flex;align-items:center;gap:8px;font-weight:900;color:var(--navy);font-size:20px}
.brand .dot{width:22px;height:22px;border-radius:50%;background:var(--teal)}
.nav{position:absolute;top:37px;left:0;font-size:16px;color:#2b2f3d;font-weight:500}
.nav a{position:absolute;white-space:nowrap;color:inherit;text-decoration:none}
.nav a.active{color:var(--teal)}

/* hero */
.hero{position:absolute;top:93px;left:0;width:1200px;height:640px;background:linear-gradient(200deg,#137873 0%,#176466 30%,#1b3e6b 65%,#1c2a62 100%)}
.hero-visual{position:absolute;left:0;top:150px;width:510px;height:560px;border-radius:0 200px 0 0;background:linear-gradient(160deg,#e6ecef 0%,#c9d3da 50%,#9fb0bc 100%);opacity:.9}
.hero-title{position:absolute;left:588px;top:222px;width:480px;color:#fff;font-weight:900;font-size:35px;line-height:41px;letter-spacing:-.3px}
.check-label{position:absolute;left:588px;top:368px;color:#fff;font-weight:800;font-size:21px}
.name-input{position:absolute;left:588px;top:427px;width:245px;height:52px;border:2px solid #fff;border-radius:26px;color:#fff;font-size:12px;font-style:italic;font-weight:600;padding:17px 18px}
.check-btn{left:837px;top:427px;width:219px;height:52px;background:#1a7b76;font-size:16px}

/* about */
.about-bg{position:absolute;top:670px;left:0;width:1200px;height:645px}
.about-lead{position:absolute;left:140px;top:822px;font-style:italic;font-weight:700;color:var(--teal);font-size:26px;line-height:41px}
.about-visual{position:absolute;left:0;top:935px;width:490px;height:378px;background:linear-gradient(150deg,#555a60 0%,#2f3236 55%,#1a1c1f 100%);clip-path:polygon(0 30%,45% 0,100% 25%,100% 100%,0 100%)}
.section-title{font-weight:900;color:var(--navy-deep);font-size:38px;letter-spacing:-.4px}
.about-title{position:absolute;left:580px;top:818px}
.about-copy{position:absolute;left:580px;top:890px;width:445px;font-size:15.5px;line-height:27px;color:#2d3140}
.about-copy p+p{margin-top:27px}

/* benefits */
.benefits-title{position:absolute;left:0;top:1410px;width:1200px;text-align:center}
.benefit{position:absolute;top:1500px;width:270px;text-align:center}
.benefit .icon{width:130px;height:130px;margin:15px auto 0;border-radius:50%;background:linear-gradient(160deg,#eef1f4 0%,#dfe5ec 100%)}
.benefit h3{margin-top:30px;font-size:21px;font-weight:700;color:var(--navy-deep)}
.benefit p{margin-top:12px;font-size:13.5px;line-height:24.5px;color:#4a4d58}

/* plans */
.plans-band{position:absolute;left:0;top:1960px;width:1200px;height:560px}
.plans-title{position:absolute;left:170px;top:2130px;color:#fff;font-weight:900;font-size:40px;letter-spacing:-.4px}
.plans-sub{position:absolute;left:171px;top:2188px;color:#fff;font-weight:800;font-size:22px}
.promo-label{position:absolute;left:173px;top:2242px;color:#fff;font-weight:800;font-size:18px}
.promo-code{position:absolute;left:182px;top:2277px;width:164px;height:75px;border:2px dotted #fff;border-radius:20px;display:flex;align-items:center;justify-content:center;color:#fff;font-weight:800;font-size:22px}
.plan{position:absolute;width:282px;background:#fff;border-radius:34px;text-align:center;box-shadow:0 6px 18px rgba(0,0,0,.08)}
.plan .price{width:120px;height:120px;margin:20px auto 0;border-radius:50%;background:#dceceb;display:flex;flex-direction:column;align-items:center;justify-content:center;color:var(--teal);font-weight:900;font-size:28px}
.plan .price small{font-size:8.5px;font-weight:500;font-style:italic;color:#444;margin-top:2px}
.plan h3{margin-top:24px;font-size:23px;font-weight:800;color:var(--ink)}
.plan p{margin-top:12px;font-size:15px;line-height:22px;color:#4a4d58}
.plan .btn{position:relative;margin:22px auto 0;width:150px;height:43px;font-size:15px}

/* testimonials */
.quote-title{position:absolute;left:0;top:2740px;width:1200px;text-align:center;font-weight:900;color:var(--navy-deep);font-size:38px;letter-spacing:-.4px}
.quote-mark{color:var(--teal);font-style:italic;font-size:60px;font-weight:900;vertical-align:-14px;margin:0 26px}
.quote-text{position:absolute;left:260px;top:2816px;width:680px;text-align:center;font-style:italic;font-size:16.5px;line-height:31px;color:#2d3140}
.quote-author{position:absolute;left:0;top:3040px;width:1200px;text-align:center;color:var(--teal);font-weight:800;font-size:25px}

/* promise */
.promise{position:absolute;left:0;top:3270px;width:1200px;text-align:center}
.promise h2{color:var(--teal);font-weight:900;font-size:31px;letter-spacing:-.3px}
.promise p{color:#a9a9a9;font-weight:900;font-size:31px;letter-spacing:-.3px;margin-top:4px}

/* footer */
.footer-bg{position:absolute;left:0;top:3440px;width:1200px;height:404px}
.foot-brand{position:absolute;left:193px;top:3560px;display:flex;align-items:center;gap:12px;color:#fff;font-weight:900;font-size:34px}
.foot-brand .dot{width:34px;height:34px;border-radius:50%;border:4px solid #fff}
.pay-badge{position:absolute;top:3672px;height:36px;border-radius:6px}
.divider{position:absolute;top:3555px;width:1px;height:175px;background:#3a4262}
.foot-col{position:absolute;font-size:14px;line-height:25px;color:#e6e8ef}
.foot-col .label{color:#3aa6b8}
.foot-col a{color:#3aa6b8}
.partner{display:flex;align-items:center;gap:10px;margin-top:12px;font-weight:800;font-size:24px;color:#3aa6b8}
.partner .dot{width:36px;height:36px;border-radius:50%;background:#3aa6b8}
.copyright{position:absolute;left:178px;top:3806px;font-size:14px;color:#e6e8ef}
.social{position:absolute;top:3804px;font-size:15px;font-weight:800;color:#fff}
</style>
</head>
<body>

<header class="site-header">
  <div class="brand" style="left:172px;top:34px"><span class="dot"></span>TapLedger</div>
  <nav class="nav">
    <a class="active" style="left:337px">Home</a>
    <a style="left:422px">Partners</a>
    <a style="left:523px">Benefits</a>
    <a style="left:623px">Plans</a>
    <a style="left:701px">Testimonials</a>
    <a style="left:831px">Log in</a>
  </nav>
  <a class="btn btn-navy" style="left:907px;top:25px;width:120px;height:45px;font-size:15px">Sign up</a>
</header>

<section class="hero"></section>
<div class="hero-visual" role="img" aria-label="Hand holding a smartphone showing the TapLedger app start screen"></div>
<h1 class="hero-title">Instantly Share All Your<br>Business Contact Details<br>with 1 ‘QUICK’ TEXT</h1>
<div class="check-label">Check 'YOUR UNIQUE NAME'</div>
<div class="name-input">Keyword</div>
<a class="btn check-btn">Check availability</a>

<svg class="about-bg" viewBox="0 0 1200 645" preserveAspectRatio="none" aria-hidden="true">
  <path d="M0 0 C300 40 500 70 650 62 C850 50 1050 10 1200 -2 L1200 645 L0 645 Z" fill="var(--mint)"/>
  <circle cx="1080" cy="440" r="300" fill="var(--mint-dark)" opacity=".45"/>
</svg>
<section class="about">
  <div class="about-lead">Virtual Business Card' or<br>&nbsp;'TapLedger' is the Digital Solution.</div>
  <div class="about-visual" role="img" aria-label="Smartphone lying at an angle showing the TapLedger screen"></div>
  <h2 class="section-title about-title">About TapLedger</h2>
  <div class="about-copy">
    <p>TapLedger is the intelligent, relevant and easy way for your new customers or friends to receive ALL of your contact card information and in to a few clicks, be saved to their phones. This can be done anytime and anywhere, within Australia.</p>
    <p>Some TapLedger clients advertise this powerful tool for their business on vehicles, billboards, store frontage, websites, social media, company uniforms or just anywhere (ie text 'builder' to 420 555 010).</p>
  </div>
  <a class="btn btn-teal" style="left:574px;top:1153px;width:143px;height:44px;font-size:14px">Read more</a>
</section>

<section class="benefits">
  <h2 class="section-title benefits-title">Simple Benefits Are</h2>

  <div class="benefit" style="left:157px">
    <div class="icon" role="img" aria-label="Illustration of secure card payment"></div>
    <h3>Secure Payment</h3>
    <p>Back by the global Quillpay payment gateway. Quillpay a certified as a PCI Level One Service Provider. This is the most stringent level of certification</p>
  </div>

  <div class="benefit" style="left:465px">
    <div class="icon" role="img" aria-label="Illustration of digital marketing"></div>
    <h3>Marketing</h3>
    <p>Your keyword to all your marketing to increase sales. Some suggestions are through email signature, social media, networking, advertisements.</p>
  </div>

  <div class="benefit" style="left:779px">
    <div class="icon" role="img" aria-label="Illustration of secure cloud data storage"></div>
    <h3>Data Safe</h3>
    <p>All data is held on a secure Cirrus Cloud infrastructure in Sydney, which puts strong safeguards in place to protect your customer privacy.</p>
  </div>

  <a class="btn btn-teal" style="left:506px;top:1873px;width:189px;height:45px;font-size:14px">View all benefits</a>
</section>

<svg class="plans-band" viewBox="0 0 1200 560" preserveAspectRatio="none" aria-hidden="true">
  <defs>
    <linearGradient id="plansGrad" x1="0" y1="0" x2="1" y2="0">
      <stop offset="0" stop-color="#1c2a62"/><stop offset=".5" stop-color="#1b4a70"/><stop offset="1" stop-color="#137873"/>
    </linearGradient>
  </defs>
  <path d="M0 0 C400 50 800 50 1200 -5 L1200 580 L0 580 Z" fill="var(--mint)"/>
  <path d="M0 0 C400 50 800 50 1200 -5 L1200 460 C900 540 500 560 0 510 Z" fill="url(#plansGrad)"/>
</svg>
<div class="abs" style="left:0;top:2500px;width:1200px;height:690px;background:var(--mint)"></div>
<section class="plans">
  <div class="plans-title">Plans For Everyone</div>
  <div class="plans-sub">with great pricing</div>
  <div class="promo-label">Use offer Promo code</div>
  <div class="promo-code">HKSR125</div>

  <div class="plan" style="left:757px;top:2085px;height:360px">
    <div class="price">$6.99<small>+ gst / month</small></div>
    <h3>Business Plan</h3>
    <p>Provides for one personal<br>and business keyword.</p>
    <a class="btn btn-teal">Get started</a>
  </div>

  <div class="plan" style="left:450px;top:2251px;height:362px">
    <div class="price">$4.99<small>+ gst / month</small></div>
    <h3>Personal Plan</h3>
    <p>Provides for one keyword<br>and one personal TapLedger.</p>
    <a class="btn btn-teal">Get started</a>
  </div>
</section>

<section class="testimonials">
  <div class="quote-title"><span class="quote-mark">“</span>Our Clients love us!<span class="quote-mark">”</span></div>
  <svg class="abs" style="left:118px;top:2855px" width="42" height="80" viewBox="0 0 42 80" aria-hidden="true"><polyline points="40,2 2,40 40,78" fill="none" stroke="#2b3a5a" stroke-width="1.5"/></svg>
  <svg class="abs" style="left:1012px;top:2855px" width="42" height="80" viewBox="0 0 42 80" aria-hidden="true"><polyline points="2,2 40,40 2,78" fill="none" stroke="#2b3a5a" stroke-width="1.5"/></svg>
  <p class="quote-text">This service gained me 10 listings for me over the past year! For me is the best and most powerful tool available in the Real Estate industry. I often get caught out in social occasions, bars, restaurants, expos, the beach, everywhere without a business card, but with TapLedger I can instantly have all my details sent directly to my potential customers phone and most powerfully a web link directly to my profile page with all my listings. I would highly recommend it to anyone.</p>
  <div class="quote-author">-Mara Wilcott</div>
</section>

<section class="promise">
  <h2>We Promise 100% Satisfaction.</h2>
  <p>There is no contract and cancel anytime!</p>
</section>
<a class="btn btn-navy" style="left:487px;top:3372px;width:226px;height:44px;font-size:14px">Get started here</a>

<svg class="footer-bg" viewBox="0 0 1200 404" preserveAspectRatio="none" aria-hidden="true">
  <path d="M0 10 C400 -5 800 -5 1200 12 L1200 404 L0 404 Z" fill="var(--footer)"/>
</svg>
<footer>
  <div class="foot-brand"><span class="dot"></span>TapLedger</div>
  <div class="pay-badge" style="left:193px;width:56px;background:#e8eaf0"></div>
  <div class="pay-badge" style="left:256px;width:56px;background:#e8eaf0"></div>
  <div class="pay-badge" style="left:320px;width:40px;background:#3b7fc4"></div>

  <div class="divider" style="left:413px"></div>
  <div class="divider" style="left:732px"></div>

  <div class="foot-col" style="left:455px;top:3528px">
    TapLedger Technology Pty Limited<br>
    ABN: 12 345 678 901
    <div class="label" style="margin-top:22px">Postal Address:</div>
    PO BOX 4410 Harbourview QLD
    <div style="margin-top:22px">Contact Us</div>
    <a>email: support@tapledger.com.au</a>
  </div>

  <div class="foot-col" style="left:783px;top:3528px">
    <div class="label">Registered Address:</div>
    <div style="margin-top:6px">218 Seabreeze Terrace</div>
    <div style="margin-top:6px">Coral Point, Harbourview QLD 4299</div>
    <div style="margin-top:22px">Our Partners</div>
    <div class="partner"><span class="dot"></span>BackTrack</div>
  </div>

  <div class="copyright">© Copyright 2020 TapLedger. Terms and Conditions; Privacy Policy</div>
  <div class="social" style="left:953px">CB</div>
  <div class="social" style="left:999px">SG</div>
</footer>

</body>
</html>
```